Indy Film Production Company/Studio

We need a business card designed from an existing logo. We are a digital studio/production company that caters to creating genre entertainment, like Action, Horror, and martial arts. The card along with the logo will be used to Brand the company from letter heads to banners. The design will also be used for postcards and Brochures. It should be professional and masculine.
Updates

Thank you to all the designers who have participated. I'm narrowing down who it will be. Thank you again.

Target Market(s)

Investors, Networks, Producers, and actors

Industry/Entity Type

Film Production

Contact Information for Business Card

Teodoro Valbuena
Producer/Writer/Director
www.kestrelpicturehouse.example

Requirements
Must have
• Website address, Facebook icon and Twitter icon possibly in the back of the card.
Nice to have
• Logline of Company: Follow The Action.

```html
<!DOCTYPE html>
<html lang="en">
<head>
<meta charset="utf-8">
<title>Kestrel Picture House – Business Card</title>
<link rel="stylesheet" href="https://fonts.googleapis.com/css2?family=Roboto:ital,wght@0,400;0,500;0,900;1,400;1,700&display=swap">
<style>
  :root {
    --page-bg: #d8d5d1;
    --card-bg-top: #f3f4f5;
    --card-bg-bottom: #e6e8ea;
    --brand-red: #d01f26;
    --ink: #2a2a2a;
    --band-black: #151515;
  }
  html, body {
    margin: 0;
    padding: 0;
    width: 1200px;
    height: 969px;
    overflow: hidden;
    background: var(--page-bg);
  }
  .canvas {
    position: relative;
    width: 1200px;
    height: 969px;
  }
  .card {
    position: absolute;
    left: 100px;
    top: 200px;
    width: 1000px;
    height: 568px;
    background: linear-gradient(180deg, var(--card-bg-top), var(--card-bg-bottom));
    box-shadow: 0 2px 10px rgba(0,0,0,0.12);
    overflow: hidden;
    font-family: "Roboto", Arial, sans-serif;
  }
  .brand {
    position: absolute;
    left: 62px;
    top: 62px;
    margin: 0;
    color: var(--brand-red);
    font-weight: 900;
    font-size: 64px;
    line-height: 1.02;
    letter-spacing: 1px;
    text-transform: uppercase;
  }
  .person {
    position: absolute;
    left: 62px;
    top: 350px;
  }
  .person-name {
    margin: 0;
    color: var(--brand-red);
    font-weight: 700;
    font-style: italic;
    font-size: 31px;
    letter-spacing: 0.5px;
    text-transform: uppercase;
  }
  .person-role {
    margin: 8px 0 0;
    color: var(--ink);
    font-weight: 400;
    font-size: 23px;
    text-transform: uppercase;
  }
  .contact {
    position: absolute;
    left: 578px;
    top: 348px;
    margin: 0;
    padding: 0;
    list-style: none;
  }
  .contact-item {
    display: flex;
    align-items: center;
    height: 39px;
    color: var(--ink);
    font-style: italic;
    font-size: 23px;
  }
  .contact-icon {
    width: 22px;
    height: 22px;
    margin-right: 14px;
    fill: var(--brand-red);
    flex: none;
  }
  .card-band {
    position: absolute;
    left: 0;
    bottom: 0;
    width: 1000px;
    height: 26px;
  }
</style>
</head>
<body>
<div class="canvas">
  <section class="card" aria-label="Business card">
    <h1 class="brand">Kestrel<br>Picture House</h1>

    <div class="person">
      <p class="person-name">Teodoro Valbuena</p>
      <p class="person-role">Producer/Writer/Director</p>
    </div>

    <ul class="contact">
      <li class="contact-item">
        <svg class="contact-icon" viewBox="0 0 24 24" aria-hidden="true">
          <path d="M3 7c0-2 2-3 9-3s9 1 9 3v2h-5V7.5C14.5 7 9.5 7 8 7.5V9H3z"/>
          <path d="M6 11h12l2 9H4z"/>
          <circle cx="12" cy="15" r="2.3" fill="#fff"/>
        </svg>
        555 0142 7789
      </li>
      <li class="contact-item">
        <svg class="contact-icon" viewBox="0 0 24 24" aria-hidden="true">
          <path d="M2 5h20v14H2z"/>
          <path d="M2 5l10 8 10-8" fill="none" stroke="#fff" stroke-width="1.8"/>
        </svg>
        teodoro@kestrelpicture.example
      </li>
      <li class="contact-item">
        <svg class="contact-icon" viewBox="0 0 24 24" aria-hidden="true">
          <circle cx="12" cy="12" r="10"/>
          <path d="M2 12h20M12 2c-4 5-4 15 0 20M12 2c4 5 4 15 0 20" fill="none" stroke="#fff" stroke-width="1.5"/>
        </svg>
        www.kestrelpicturehouse.example
      </li>
    </ul>

    <svg class="card-band" viewBox="0 0 1000 26" preserveAspectRatio="none" aria-hidden="true">
      <rect x="0" y="0" width="1000" height="26" fill="var(--band-black)"/>
      <polygon points="0,0 768,0 752,26 0,26" fill="var(--brand-red)"/>
    </svg>
  </section>
</div>
</body>
</html>
```